Quillhaven Air Business Card Design

Design new, 2 sides, business cards for a residential and light commercial heating, air conditioning contractor.

Target Market(s)

Homeowners, small businesses

Industry/Entity Type

Business

Contact Information for Business Card

Dominic Westerhall
Phone - 862-415-2736
Email
Address - PO box 518
Brightwater NJ 07912
Website - www.QuillhavenAirLLC.example

Requirements
Must have
• logo, company colors, standard size with no die cut, so I can use nova stamp

```html
<!DOCTYPE html>
<html lang="en">
<head>
<meta charset="utf-8">
<title>Quillhaven Air Business Card</title>
<link rel="stylesheet" href="https://fonts.googleapis.com/css2?family=Montserrat:wght@400;600;700&display=swap">
<style>
  :root {
    --stage: #ece8e4;
    --black: #050303;
    --wine: #7a1420;
    --wine-deep: #4a0a12;
    --glow: #8c2a14;
    --cream: #f3e2b8;
    --white: #f6f1ea;
    --rule: rgba(246, 241, 234, 0.55);
  }
  * { margin: 0; padding: 0; box-sizing: border-box; }
  html, body { width: 1200px; height: 913px; overflow: hidden; }
  body {
    background: var(--stage);
    font-family: "Montserrat", sans-serif;
    position: relative;
  }
  .card {
    position: absolute;
    width: 560px;
    height: 320px;
    border-radius: 4px;
    overflow: hidden;
    box-shadow: 0 10px 30px rgba(0,0,0,0.25);
  }
  .card--front {
    left: 60px; top: 70px;
    background: radial-gradient(ellipse 48% 52% at 50% 45%, var(--glow) 0%, #4a140a 45%, var(--black) 100%);
    display: flex; align-items: center; justify-content: center;
  }
  .brand {
    display: flex; align-items: center; gap: 14px;
    color: var(--cream);
    font-weight: 700;
    letter-spacing: 0.04em;
    text-transform: uppercase;
    white-space: nowrap;
  }
  .brand__dot {
    width: 14px; height: 14px; border-radius: 50%;
    background: var(--cream);
    flex: none;
  }
  .card--front .brand { font-size: 40px; }
  .card--back {
    right: 60px; top: 520px;
    background: var(--black);
  }
  .card--back .backdrop { position: absolute; inset: 0; }
  .card--back .brand {
    position: absolute; right: 26px; top: 34px;
    font-size: 19px; gap: 9px;
  }
  .card--back .brand__dot { width: 9px; height: 9px; }
  .address {
    position: absolute; right: 26px; top: 74px;
    text-align: right;
    color: var(--cream);
    font-size: 12px; line-height: 1.45;
  }
  .contact {
    position: absolute; left: 34px; bottom: 36px; width: 330px;
    color: var(--white);
  }
  .contact__rule { height: 1px; background: var(--rule); }
  .contact__name {
    font-size: 20px; font-weight: 400;
    padding: 10px 0 9px;
  }
  .contact__name strong { font-weight: 700; color: var(--cream); letter-spacing: 0.03em; }
  .contact__list { list-style: none; padding-top: 10px; font-size: 13px; }
  .contact__list li { display: flex; align-items: center; gap: 8px; margin-bottom: 4px; }
  .contact__list svg { width: 13px; height: 13px; flex: none; }
</style>
</head>
<body>
  <section class="card card--front" aria-label="Business card front">
    <div class="brand"><span class="brand__dot"></span>Quillhaven Air</div>
  </section>

  <section class="card card--back" aria-label="Business card back">
    <svg class="backdrop" viewBox="0 0 560 320" preserveAspectRatio="none" aria-hidden="true">
      <defs>
        <radialGradient id="wineGlow" cx="0.33" cy="0.42" r="0.7">
          <stop offset="0" stop-color="#b5402a"/>
          <stop offset="0.45" stop-color="#7a1420"/>
          <stop offset="1" stop-color="#4a0a12"/>
        </radialGradient>
      </defs>
      <rect width="560" height="320" fill="url(#wineGlow)"/>
      <path d="M250,0 C330,70 430,150 560,205 L560,0 Z" fill="#050303"/>
      <path d="M232,0 C320,85 420,165 560,222" fill="none" stroke="#050303" stroke-width="6"/>
      <path d="M262,0 C340,60 440,140 560,188" fill="none" stroke="#7a1420" stroke-width="5"/>
    </svg>
    <div class="brand"><span class="brand__dot"></span>Quillhaven Air</div>
    <p class="address">PO box 518<br>Brightwater<br>NJ 07912</p>
    <div class="contact">
      <div class="contact__rule"></div>
      <p class="contact__name">Dominic <strong>WESTERHALL</strong></p>
      <div class="contact__rule"></div>
      <ul class="contact__list">
        <li>
          <svg viewBox="0 0 16 16" aria-hidden="true"><circle cx="8" cy="8" r="7.5" fill="#f6f1ea"/><path d="M5.2 4.2l1.4-.4 1 2-1 .8c.5 1.1 1.2 1.8 2.3 2.3l.8-1 2 1-.4 1.4c-2.8.3-6.4-3.3-6.1-6.1z" fill="#4a0a12"/></svg>
          862-415-2736
        </li>
        <li>
          <svg viewBox="0 0 16 16" aria-hidden="true"><circle cx="8" cy="8" r="7.5" fill="#f6f1ea"/><circle cx="8" cy="8" r="5" fill="none" stroke="#4a0a12" stroke-width="1.2"/><path d="M3 8h10M8 3c-2 2.8-2 7.2 0 10M8 3c2 2.8 2 7.2 0 10" fill="none" stroke="#4a0a12" stroke-width="1"/></svg>
          www.QuillhavenAirLLC.example
        </li>
      </ul>
    </div>
  </section>
</body>
</html>
```